SkyvornQ Business Cards and Stationary Design

Need a design for our business cards and stationary. I want to carry on the theme of the logo. I want the business cards to have a design on the back. I would like the business cards and the stationary to carry the same theme, design scheme, and branding

Target Market(s)

Airlines and Maintenance Facilities

Industry/Entity Type

Aviation

Contact Information for Business Card

Name
Position Title
Address: 4827 Trellis Hollow Road, Brenwick Falls, Ohio, 45219
Office Number
Mobile Number
Email
Website

Font styles to use
Serif
Sans Serif

Colors

Designer to choose colors to be used in the design.

```html
<!DOCTYPE html>
<html lang="en">
<head>
<meta charset="utf-8">
<title>SkyvornQ Business Card</title>
<link rel="stylesheet" href="https://fonts.googleapis.com/css2?family=Saira:wght@500;600;700&family=Open+Sans:ital,wght@0,400;0,600;0,700;1,400&display=swap">
<style>
  :root {
    --backdrop: #3b3c3e;
    --card: #1d1e21;
    --silver: #8d9095;
    --white: #f1f2f4;
    --muted: #c9cbcf;
    --sky: #1e9be0;
    --navy: #152a55;
  }
  * { margin: 0; padding: 0; box-sizing: border-box; }
  html, body { width: 799px; height: 1200px; overflow: hidden; }
  body {
    background: var(--backdrop);
    position: relative;
    font-family: "Open Sans", sans-serif;
  }
  .card {
    position: absolute;
    left: 90px;
    width: 620px;
    height: 354px;
    background: var(--card);
    border-radius: 22px;
    overflow: hidden;
    box-shadow: 0 14px 30px rgba(0,0,0,.45);
  }
  .card--front { top: 150px; }
  .card--back { top: 700px; }

  .front-brand {
    position: absolute;
    inset: 0;
    display: flex;
    align-items: center;
    justify-content: center;
    gap: 18px;
  }
  .brand-mark {
    width: 46px; height: 46px;
    border-radius: 50%;
    border: 4px solid var(--silver);
  }
  .front-brand .brand-name {
    font-family: "Saira", sans-serif;
    font-weight: 700;
    font-size: 54px;
    letter-spacing: 6px;
    color: var(--silver);
  }

  .back-brand {
    position: absolute;
    top: 42px; left: 40px;
    display: flex;
    align-items: center;
    gap: 16px;
  }
  .back-brand .brand-name {
    font-family: "Saira", sans-serif;
    font-weight: 700;
    font-size: 50px;
    letter-spacing: 6px;
    color: var(--white);
  }
  .back-brand .brand-mark { border-color: var(--sky); width: 52px; height: 52px; }

  .bands { position: absolute; inset: 0; }

  .person {
    position: absolute;
    left: 40px; top: 194px;
  }
  .person-name {
    font-weight: 700;
    font-size: 24px;
    color: var(--sky);
    line-height: 1.1;
  }
  .person-title {
    font-size: 14px;
    color: var(--muted);
    margin-top: 2px;
  }

  .contact {
    position: absolute;
    left: 352px; top: 166px;
    list-style: none;
    font-size: 14px;
    color: var(--muted);
    line-height: 1.35;
  }
  .contact li { display: flex; align-items: center; gap: 8px; }
  .contact svg { width: 13px; height: 13px; fill: var(--sky); flex: none; }
  .contact .address { display: block; margin-top: 2px; }

  .website {
    position: absolute;
    right: 70px; bottom: 17px;
    font-size: 15px;
    color: var(--white);
    letter-spacing: .3px;
  }
</style>
</head>
<body>

<section class="card card--front" aria-label="Business card front">
  <div class="front-brand">
    <span class="brand-mark"></span>
    <span class="brand-name">SKYVORNQ</span>
  </div>
</section>

<section class="card card--back" aria-label="Business card back">
  <svg class="bands" viewBox="0 0 620 354" aria-hidden="true">
    <rect x="0" y="266" width="270" height="12" fill="var(--sky)"/>
    <path d="M250 354 L250 300 Q250 278 272 278 L620 278 L620 354 Z" fill="var(--navy)"/>
  </svg>

  <div class="back-brand">
    <span class="brand-name">SKYVORNQ</span>
    <span class="brand-mark"></span>
  </div>

  <div class="person">
    <p class="person-name">Dorian Pelkey</p>
    <p class="person-title">Managing Director</p>
  </div>

  <ul class="contact">
    <li>
      <svg viewBox="0 0 16 16" aria-hidden="true"><path d="M3 1h3l1.5 4-2 1.3a9 9 0 0 0 4.2 4.2L11 8.5l4 1.5v3a2 2 0 0 1-2 2A12 12 0 0 1 1 3a2 2 0 0 1 2-2z"/></svg>
      5551 2034 876
    </li>
    <li>
      <svg viewBox="0 0 16 16" aria-hidden="true"><path d="M4 0h8a1 1 0 0 1 1 1v14a1 1 0 0 1-1 1H4a1 1 0 0 1-1-1V1a1 1 0 0 1 1-1zm1 2v10h6V2zm3 11a1 1 0 1 0 0 2 1 1 0 0 0 0-2z"/></svg>
      5559 4417 302
    </li>
    <li>
      <svg viewBox="0 0 16 16" aria-hidden="true"><path d="M0 3h16v10H0zm1.5 1.2V12h13V4.2L8 9z"/></svg>
      dorian@skyvornq.com
    </li>
    <li class="address">4827 Trellis Hollow Road,<br>Brenwick Falls, Ohio, 45219</li>
  </ul>

  <p class="website">www.skyvornq.com</p>
</section>

</body>
</html>
```